Restyle corporate identity (+ logo) for a road construction company

We need a new logo and stationary design for our company VARNOK path. VARNOK path® increases the road base strength, while reducing major costs and time of road construction. Attached some examples of the current design.

Our wishes for the new logo:
- Business look
- Style sheet
- Modern

More information: www.varnokpath.example
Updates

Target Market(s)

Government

Industry/Entity Type

Construction

Requirements
Must have
• Logo (with road sign) + text

```html
<!DOCTYPE html>
<html lang="en">
<head>
<meta charset="utf-8">
<title>VARNOK path – Business Card</title>
<link rel="stylesheet" href="https://fonts.googleapis.com/css2?family=Open+Sans:wght@400;600;700&display=swap">
<style>
  :root {
    --backdrop: #8c8c8c;
    --card: #eaeaed;
    --brand-blue: #1f7fe0;
    --text-dark: #3a3a3a;
    --text-muted: #8a8a8a;
  }
  * { box-sizing: border-box; margin: 0; padding: 0; }
  html, body {
    width: 1105px;
    height: 1200px;
    overflow: hidden;
    background: var(--backdrop);
    font-family: "Open Sans", Arial, sans-serif;
  }
  .card {
    position: absolute;
    left: 182px;
    width: 746px;
    height: 427px;
    background: var(--card);
    box-shadow: 0 6px 14px rgba(0,0,0,0.25);
  }
  .card--front { top: 119px; }
  .card--back { top: 637px; }

  .accent-bar {
    position: absolute;
    left: 0;
    top: 150px;
    width: 15px;
    height: 52px;
    background: var(--brand-blue);
  }
  .contact-block {
    position: absolute;
    left: 42px;
    top: 150px;
    width: 290px;
    color: var(--text-dark);
  }
  .person-name {
    font-size: 26px;
    font-weight: 600;
    color: var(--brand-blue);
    line-height: 30px;
  }
  .person-role {
    font-size: 19px;
    color: var(--text-muted);
    line-height: 24px;
  }
  .address {
    margin-top: 14px;
    font-size: 18px;
    line-height: 26px;
    font-style: normal;
  }
  .contact-list {
    list-style: none;
    margin-top: 14px;
    font-size: 18px;
    line-height: 28px;
    white-space: nowrap;
  }
  .contact-list li {
    display: flex;
    align-items: center;
    gap: 9px;
  }
  .contact-list svg { width: 17px; height: 17px; fill: var(--brand-blue); flex: none; }

  .front-brand {
    position: absolute;
    left: 349px;
    top: 30px;
    width: 369px;
    height: 373px;
    display: flex;
    flex-direction: column;
    align-items: center;
    justify-content: center;
    gap: 14px;
  }
  .front-brand__square {
    width: 92px;
    height: 92px;
    background: var(--brand-blue);
  }
  .front-brand__name {
    font-size: 72px;
    font-weight: 700;
    line-height: 84px;
    color: var(--brand-blue);
    text-align: center;
    letter-spacing: 2px;
  }

  .back-brand {
    position: absolute;
    inset: 0;
    display: flex;
    align-items: center;
    justify-content: center;
    gap: 18px;
  }
  .back-brand__square {
    width: 100px;
    height: 100px;
    background: var(--brand-blue);
  }
  .back-brand__name {
    font-size: 50px;
    font-weight: 700;
    line-height: 56px;
    color: var(--brand-blue);
    letter-spacing: 2px;
  }
</style>
</head>
<body>
  <section class="card card--front">
    <div class="accent-bar"></div>
    <div class="contact-block">
      <h1 class="person-name">MAREN HOLT</h1>
      <p class="person-role">CEO/Founder</p>
      <address class="address">
        Lindenkade 58<br>
        3012 AB Veldstad<br>
        The Netherlands
      </address>
      <ul class="contact-list">
        <li>
          <svg viewBox="0 0 24 24" aria-hidden="true"><path d="M6.6 10.8a15.1 15.1 0 0 0 6.6 6.6l2.2-2.2a1 1 0 0 1 1-.25 11.4 11.4 0 0 0 3.6.57 1 1 0 0 1 1 1V20a1 1 0 0 1-1 1A17 17 0 0 1 3 4a1 1 0 0 1 1-1h3.5a1 1 0 0 1 1 1c0 1.25.2 2.45.57 3.6a1 1 0 0 1-.25 1z"/></svg>
          555 014 2290
        </li>
        <li>
          <svg viewBox="0 0 24 24" aria-hidden="true"><path d="M2 5h20v14H2z"/><path d="M3 6.5 12 13l9-6.5" fill="none" stroke="#eaeaed" stroke-width="1.6"/></svg>
          maren@varnokpath.example
        </li>
        <li>
          <svg viewBox="0 0 24 24" aria-hidden="true"><circle cx="12" cy="12" r="10"/><path d="M2 12h20M12 2c3 3 3 17 0 20M12 2c-3 3-3 17 0 20" fill="none" stroke="#eaeaed" stroke-width="1.4"/></svg>
          www.varnokpath.example
        </li>
      </ul>
    </div>
    <div class="front-brand">
      <span class="front-brand__square"></span>
      <span class="front-brand__name">VARNOK<br>PATH</span>
    </div>
  </section>

  <section class="card card--back">
    <div class="back-brand">
      <span class="back-brand__square"></span>
      <span class="back-brand__name">VARNOK<br>PATH</span>
    </div>
  </section>
</body>
</html>
```